Upmarket Dessert Lounge needs a Business Card Design

We are an upmarket dessert lounge needing a business card to match our image.

We want something that is simple yet beautiful, feminine, classy, sophisticated and elegant. We want it to stand out and don't mind if it is bold.

The design should include our logo and colours of red or maroon with gold highlights. We don't mind if black is used.

Marlow & Quince

Target Market(s)

For those who like to indulge or treat themselves and give in to their temptations on good quality desserts.

Industry/Entity Type

Business

Requirements
Must have
• Must include our logo and our name

Marlow & Quince

M & Q

```html
<!DOCTYPE html>
<html lang="en">
<head>
<meta charset="utf-8">
<title>Marlow &amp; Quince – Business Card</title>
<link href="https://fonts.googleapis.com/css2?family=Source+Sans+3:wght@400;600;700&display=swap" rel="stylesheet">
<style>
  :root {
    --backdrop: #d6d6d6;
    --card: #000000;
    --maroon: #7a1518;
    --peach: #fdd39b;
    --gold: #f5c77e;
    --white: #ffffff;
  }
  * { margin: 0; padding: 0; box-sizing: border-box; }
  html, body { width: 956px; height: 1200px; overflow: hidden; }
  body {
    position: relative;
    background: var(--backdrop);
    font-family: "Source Sans 3", "Myriad Pro", sans-serif;
  }
  .card {
    position: absolute;
    left: 75px;
    width: 797px;
    height: 456px;
    background: var(--card);
    border-radius: 28px;
    overflow: hidden;
  }
  .card--front { top: 87px; }
  .card--back { top: 634px; }

  .side-strip {
    position: absolute; top: 0; right: 0;
    width: 60px; height: 100%;
    background: var(--peach);
  }
  .side-rule {
    position: absolute; left: 729px;
    width: 8px; background: var(--maroon);
  }
  .side-rule--top { top: 0; height: 151px; }
  .side-rule--bottom { top: 305px; height: 151px; }

  .brand-name {
    position: absolute;
    color: var(--gold);
    font-weight: 600;
    white-space: nowrap;
    text-align: center;
  }
  .card--front .brand-name {
    left: 42px; width: 388px; top: 135px;
    font-size: 38px; letter-spacing: 1px;
  }
  .card--back .brand-name {
    left: 0; width: 100%; top: 158px;
    font-size: 110px; line-height: 1;
  }

  .person { position: absolute; right: 82px; top: 76px; text-align: right; }
  .person__name { color: var(--gold); font-weight: 700; font-size: 22px; line-height: 28px; }
  .person__role { color: var(--gold); font-size: 22px; line-height: 30px; }

  .contact {
    position: absolute; right: 77px;
    color: var(--white); font-size: 19px;
    text-align: right; white-space: nowrap;
  }
  .icon { position: absolute; left: 742px; width: 20px; height: 20px; fill: var(--maroon); }

  .address {
    position: absolute; left: 101px; top: 370px;
    color: var(--white); font-size: 19px; line-height: 27px;
  }
  .address__icon { position: absolute; left: -34px; top: 14px; width: 22px; height: 20px; fill: var(--white); }
</style>
</head>
<body>

<section class="card card--front">
  <div class="side-strip"></div>
  <div class="side-rule side-rule--top"></div>
  <div class="side-rule side-rule--bottom"></div>

  <div class="brand-name">MARLOW &amp; QUINCE</div>

  <div class="person">
    <div class="person__name">Your Name</div>
    <div class="person__role">Designation</div>
  </div>

  <div class="contact" style="top:193px">123-456-7890</div>
  <svg class="icon" style="top:196px" viewBox="0 0 20 20" aria-hidden="true"><path d="M2 7c0-3 4-4 8-4s8 1 8 4v2h-4V7H6v2H2z"/><path d="M5 10h10l2 7H3z"/></svg>

  <div class="contact" style="top:229px">123-456-7890</div>
  <svg class="icon" style="top:229px" viewBox="0 0 20 20" aria-hidden="true"><path d="M6 3h8v16H6zM8 5v5h4V5zM8 12v5h4v-5z"/><rect x="9" y="0" width="2" height="3"/></svg>

  <div class="contact" style="top:265px">123-456-7890</div>
  <svg class="icon" style="top:265px" viewBox="0 0 20 20" aria-hidden="true"><path d="M5 2h10v5H5zM2 8h16v8H2zM5 13h10v5H5z"/></svg>

  <div class="contact" style="top:357px">name@yourwebsite.com</div>
  <svg class="icon" style="top:360px" viewBox="0 0 20 20" aria-hidden="true"><path d="M10 2a8 8 0 1 0 5 14l-1-2a6 6 0 1 1 2-4v1c0 1-1 1-1 0V6h-2v1a4 4 0 1 0 0 6c1 2 5 1 5-2v-1a8 8 0 0 0-8-8zm0 6a2 2 0 1 1 0 4 2 2 0 0 1 0-4z"/></svg>

  <div class="contact" style="top:390px">www.marlow&amp;quince.com</div>
  <svg class="icon" style="top:393px" viewBox="0 0 20 20" aria-hidden="true"><circle cx="10" cy="10" r="8"/></svg>

  <address class="address" style="font-style:normal">
    <svg class="address__icon" viewBox="0 0 22 20" aria-hidden="true"><path d="M11 1L1 10h3v9h5v-6h4v6h5v-9h3z"/></svg>
    0000, Street Name<br>City Name, Country Code.
  </address>
</section>

<section class="card card--back">
  <div class="brand-name">M &amp; Q</div>
</section>

</body>
</html>
```